New Business Card Design for Manufacturing

We are an engineering/manufacturing company that offers Advanced machining/assembly/engineering services, as well as innovative products for the heavy duty engine cooling markets.

We are looking to get a new business card designed that is clean and modern looking, but still fits the wide range of technical/skilled work we do.

- We hope to use this design as the base for other design work in new Presentations, web, and print work.

Industry/Entity Type

Engineering

Contact Information for Business Card

Our preferred color of blue is (RGB) 22/71/159 but can vary slightly from that color. Our content will be our Logo and full company name (Vantrell Forge Works, Inc.), company address, name, job title, phone number with extension, cell number, fax number, website, and email address on the cards.
We'd like the full company name next to the logo, but we are open to other interpretations of that layout.
Preferably, we would like the back side to be clean with just our logo, and the front to contain all of the contact information.

Colors
2f74b4
0355a3
85abd2

Requirements
Must have
• - Logo, company name, needed content - We are open to interpretation beyond that.
• - Standard size business card.
• - Horizontal orientation.
• - Enough space for lengthy names / job titles (for example, a job title could read "Directory of Human Resources" or "V.P. of Governmental Affairs"). We need this to look clean, whether the title be short (CEO) or long (as described above).

```html
<!DOCTYPE html>
<html lang="en">
<head>
<meta charset="utf-8">
<title>Vantrell Forge Works – Business Card</title>
<link rel="stylesheet" href="https://fonts.googleapis.com/css2?family=Archivo:wght@800&family=Open+Sans:wght@400;600&display=swap">
<style>
  :root {
    --bg: #e6e6e8;
    --card: #ffffff;
    --brand-blue: #0c52a0;
    --sky: #3aa8e0;
    --band-dark: #4fb3e6;
    --band-light: #a9d3f2;
    --ink: #6b6b6b;
    --ink-soft: #8a8a8a;
    --white: #ffffff;
  }
  * { box-sizing: border-box; margin: 0; padding: 0; }
  html, body { width: 1200px; height: 1000px; overflow: hidden; }
  body {
    background: var(--bg);
    position: relative;
    font-family: "Open Sans", Arial, sans-serif;
  }
  .card {
    position: absolute;
    width: 560px;
    height: 320px;
    background: var(--card);
    box-shadow: 0 10px 30px rgba(0,0,0,.18);
    overflow: hidden;
  }
  .card-front { left: 110px; top: 110px; }
  .card-back { left: 530px; top: 560px; }

  /* Front */
  .company-name {
    position: absolute; left: 36px; top: 34px;
    font-family: "Archivo", Arial, sans-serif; font-weight: 800;
    font-size: 17px; line-height: 17px; color: var(--sky);
    text-transform: uppercase; letter-spacing: .2px;
  }
  .company-name .suffix { font-size: 9px; }
  .brand-word {
    position: absolute; left: 222px; top: 30px;
    font-family: "Archivo", Arial, sans-serif; font-weight: 800;
    font-size: 34px; line-height: 1; color: var(--brand-blue);
    text-transform: uppercase;
  }
  .person { position: absolute; left: 0; right: 0; top: 94px; text-align: center; padding-left: 40px; }
  .person-name { font-size: 21px; letter-spacing: 1.5px; color: var(--ink); }
  .person-title { font-size: 11px; letter-spacing: 1.2px; color: var(--ink-soft); text-transform: uppercase; margin-top: 2px; }
  .address-band { position: absolute; left: 0; top: 140px; width: 560px; height: 60px; }
  .address {
    position: absolute; left: 190px; top: 171px; width: 315px; height: 20px;
    display: flex; align-items: center; justify-content: center; gap: 10px;
    font-size: 12px; letter-spacing: 1.3px; color: var(--white); text-transform: uppercase;
  }
  .contact-list {
    position: absolute; list-style: none;
    font-size: 12px; letter-spacing: 1.2px; color: var(--ink); text-transform: uppercase;
  }
  .contact-list li { display: flex; align-items: center; gap: 10px; height: 24px; }
  .contact-phones { left: 36px; top: 236px; }
  .contact-web { left: 330px; top: 206px; }
  .icon { width: 13px; height: 13px; fill: var(--ink); flex: none; }
  .icon-light { fill: var(--white); }

  /* Back */
  .back-panel {
    position: absolute; left: 28px; top: 28px; right: 28px; bottom: 28px;
    background: var(--brand-blue);
    display: flex; flex-direction: column; align-items: center; justify-content: center; gap: 22px;
  }
  .back-brand {
    font-family: "Archivo", Arial, sans-serif; font-weight: 800;
    font-size: 62px; line-height: 1; color: var(--white); text-transform: uppercase;
  }
  .back-url { font-size: 15px; color: var(--white); letter-spacing: .5px; }
</style>
</head>
<body>

<section class="card card-front" aria-label="Business card front">
  <div class="company-name">Vantrell<br>Forge<br>Works <span class="suffix">Inc</span></div>
  <div class="brand-word">Vantrell</div>

  <div class="person">
    <div class="person-name">NAME OF CEO</div>
    <div class="person-title">Directory of Human Resources</div>
  </div>

  <svg class="address-band" viewBox="0 0 560 60" aria-hidden="true">
    <path d="M100 60 C106 34 120 20 150 20 L500 20 C516 20 526 26 534 36 L534 60 Z" fill="var(--band-light)"/>
    <path d="M180 60 C186 38 200 26 228 26 L470 26 C490 26 502 36 508 50 L508 60 Z" fill="var(--band-dark)"/>
  </svg>
  <div class="address">
    <svg class="icon icon-light" viewBox="0 0 24 24"><path d="M12 2a7 7 0 0 0-7 7c0 5 7 13 7 13s7-8 7-13a7 7 0 0 0-7-7zm0 9.5A2.5 2.5 0 1 1 12 6.5a2.5 2.5 0 0 1 0 5z"/></svg>
    <span>Your Company Address</span>
  </div>

  <ul class="contact-list contact-phones">
    <li><svg class="icon" viewBox="0 0 24 24"><path d="M3 8c0-2 2-4 9-4s9 2 9 4v2h-5V8H8v2H3zM6 12h12l2 8H4z"/></svg>Phone Number</li>
    <li><svg class="icon" viewBox="0 0 24 24"><path d="M6.6 10.8a15 15 0 0 0 6.6 6.6l2.2-2.2c.3-.3.7-.4 1-.2 1.1.4 2.3.6 3.6.6.6 0 1 .4 1 1V20c0 .6-.4 1-1 1A17 17 0 0 1 3 4c0-.6.4-1 1-1h3.5c.6 0 1 .4 1 1 0 1.3.2 2.5.6 3.6.1.3 0 .7-.2 1z"/></svg>Cell Number</li>
    <li><svg class="icon" viewBox="0 0 24 24"><path d="M6 3h12v5H6zM3 9h18v9h-3v3H6v-3H3zm5 6v4h8v-4z"/></svg>Fax Number</li>
  </ul>

  <ul class="contact-list contact-web">
    <li><svg class="icon" viewBox="0 0 24 24"><path d="M12 2a10 10 0 1 0 0 20 10 10 0 0 0 0-20zm6.9 6h-3a15 15 0 0 0-1.3-4A8 8 0 0 1 18.9 8zM12 4c.8 1.2 1.5 2.5 1.9 4h-3.8c.4-1.5 1.1-2.8 1.9-4zM4.3 14a8 8 0 0 1 0-4h3.4a16 16 0 0 0 0 4zm.8 2h3a15 15 0 0 0 1.3 4A8 8 0 0 1 5.1 16zM8 8H5.1a8 8 0 0 1 4.3-4A15 15 0 0 0 8 8zm4 12c-.8-1.2-1.5-2.5-1.9-4h3.8c-.4 1.5-1.1 2.8-1.9 4zm2.3-6H9.7a14 14 0 0 1 0-4h4.6a14 14 0 0 1 0 4zm.3 6a15 15 0 0 0 1.3-4h3a8 8 0 0 1-4.3 4zm1.7-6a16 16 0 0 0 0-4h3.4a8 8 0 0 1 0 4z"/></svg>Website</li>
    <li><svg class="icon" viewBox="0 0 24 24"><path d="M2 5h20v14H2zm2 2v.5l8 5 8-5V7z"/></svg>Email Address</li>
  </ul>
</section>

<section class="card card-back" aria-label="Business card back">
  <div class="back-panel">
    <div class="back-brand">Vantrell</div>
    <div class="back-url">www.website.com</div>
  </div>
</section>

</body>
</html>
```